Tech Savy small Business accountant business card design

We need a business card for a new company based in the cloud. We provide tax, business advisory, accounting, information technology solutions and back office functions to small businesses. We offer fixed fee packages with add on services as you need them. By harnessing technology we simplify small business operational processes providing valuable time and information for small business owners to grow their business. In the logo (bluvoria) we want to be able to see bluv and experts. The final design should communicate achieving growth dreams and balance (ie life and $).
Updates
This project has been temporarily placed on hold until I finalize "Tech Savy small Business accountant needs a logo". I invite all designers to submit on this logo project. Once my logo is finalized I will resume this business card contest. Thanks Added Wednesday, March 19, 2014
This project has been temporarily placed on hold until I finalize "Tech Savy small Business accountant logo". I invite all designers to submit on this logo project. Once my logo is finalized I will resume this business card contest. Thanks Added Thursday, March 20, 2014
Target Market(s)
Small Business (Revenue $500,000, more than 3 employees) owners.
Industry/Entity Type
Small Business
Contact Information for Business Card
Marcy Elwind (Principal)
Accountant, Tax Agent.
TEL | 0417 683 912
EMAIL | Marcy.Elwind@bluvoria.com.au
WEB | www.bluvoria.com.au
Look and feel

```html
<!DOCTYPE html>
<html lang="en">
<head>
<meta charset="utf-8">
<title>bluvoria business card</title>
<link href="https://fonts.googleapis.com/css2?family=Quicksand:wght@500;700&display=swap" rel="stylesheet">
<style>
  :root {
    --page: #ecebe8;
    --card-white: #f7f8f9;
    --brand-blue: #1fa9d6;
    --brand-blue-light: #33bde6;
    --swoosh-grey: #a9adb2;
    --text-grey: #8a8f95;
    --card-black: #050505;
    --white: #ffffff;
  }
  * { box-sizing: border-box; margin: 0; padding: 0; }
  html, body {
    width: 1200px; height: 780px; overflow: hidden;
    background: var(--page);
    font-family: "Quicksand", "Helvetica Neue", Arial, sans-serif;
  }
  .sheet {
    width: 1200px; height: 780px;
    display: flex; align-items: center; justify-content: center; gap: 40px;
  }
  .card {
    position: relative; width: 560px; height: 320px; overflow: hidden;
    box-shadow: 0 6px 18px rgba(0,0,0,.18);
  }
  .card-front { background: var(--card-white); }
  .card-back { background: var(--card-black); display: flex; flex-direction: column; align-items: center; justify-content: center; }

  .front-waves { position: absolute; inset: 0; width: 100%; height: 100%; }

  .brand-name {
    font-weight: 700; color: var(--brand-blue); letter-spacing: -1px; line-height: 1;
  }
  .front-identity { position: absolute; left: 32px; top: 62px; }
  .front-identity .brand-name { font-size: 54px; }
  .tagline { font-weight: 500; color: var(--text-grey); font-size: 13px; margin-top: 6px; white-space: nowrap; }

  .person { position: absolute; left: 60px; top: 178px; }
  .person-name { font-size: 26px; font-weight: 500; color: var(--brand-blue); line-height: 1.1; }
  .person-role { font-size: 13px; font-weight: 500; color: var(--text-grey); line-height: 1.35; }

  .contact {
    position: absolute; right: 20px; top: 44px;
    color: var(--white); font-size: 12px; font-weight: 500;
    display: flex; flex-direction: column; align-items: flex-end; gap: 8px;
    white-space: nowrap;
  }
  .contact-address { margin-bottom: 26px; }
  .contact-line { display: flex; align-items: center; gap: 8px; }
  .contact-icon { width: 16px; height: 16px; flex: none; }

  .card-back .brand-name { font-size: 64px; }
  .card-back .tagline { font-size: 16px; margin-top: 8px; color: var(--swoosh-grey); }
</style>
</head>
<body>
<main class="sheet">
  <section class="card card-front" aria-label="Card front">
    <svg class="front-waves" viewBox="0 0 560 320" aria-hidden="true">
      <circle cx="320" cy="30" r="50" fill="#e3e8ee" opacity="0.7"/>
      <path d="M290,150 C295,230 250,290 170,320 L235,320 C290,270 305,210 290,150 Z" fill="var(--swoosh-grey)"/>
      <path d="M330,0 C300,90 310,200 220,320 L560,320 L560,0 Z" fill="var(--brand-blue)"/>
      <path d="M370,0 C330,100 340,220 280,320 L560,320 L560,0 Z" fill="var(--brand-blue-light)" opacity="0.6"/>
      <path d="M342,0 C312,90 322,200 232,320" fill="none" stroke="var(--white)" stroke-width="4"/>
    </svg>

    <div class="front-identity">
      <div class="brand-name">bluvoria</div>
      <div class="tagline">Your business and accounting partner</div>
    </div>

    <div class="person">
      <div class="person-name">Marcy Elwind</div>
      <div class="person-role">(Principal)</div>
      <div class="person-role">Accountant, Tax Agent</div>
    </div>

    <div class="contact">
      <div class="contact-address">Kestrel Bay NSW Australia</div>
      <div class="contact-line">0417 683 912
        <svg class="contact-icon" viewBox="0 0 16 16" aria-label="Phone"><rect x="0.5" y="0.5" width="15" height="15" fill="none" stroke="#fff"/><path d="M5 4 L7 6 L6 7 C7 9 8 10 9 10 L10 9 L12 11 L10.5 12.5 C7 12 4 9 3.5 5.5 Z" fill="#fff"/></svg>
      </div>
      <div class="contact-line">Marcy.Elwind@bluvoria.com.au
        <svg class="contact-icon" viewBox="0 0 16 16" aria-label="Email"><rect x="0.5" y="0.5" width="15" height="15" fill="none" stroke="#fff"/><rect x="3.5" y="5" width="9" height="6" fill="none" stroke="#fff"/><path d="M3.5 5 L8 8.5 L12.5 5" fill="none" stroke="#fff"/></svg>
      </div>
      <div class="contact-line">www.bluvoria.com.au
        <svg class="contact-icon" viewBox="0 0 16 16" aria-label="Web"><rect x="0.5" y="0.5" width="15" height="15" fill="none" stroke="#fff"/><circle cx="8" cy="8" r="4.5" fill="none" stroke="#fff"/><path d="M3.5 8 H12.5 M8 3.5 C6 6 6 10 8 12.5 M8 3.5 C10 6 10 10 8 12.5" fill="none" stroke="#fff" stroke-width="0.8"/></svg>
      </div>
    </div>
  </section>

  <section class="card card-back" aria-label="Card back">
    <div class="brand-name">bluvoria</div>
    <div class="tagline">Your business and accounting partner</div>
  </section>
</main>
</body>
</html>
```